Coastline Premier Retreats Business Card Design

Design a business card for Coastline Premier Retreats. Look at the website for colors and reference. Card should have logo, name, title, office number, mobile number, email, URL and a tagline like, "Luxury Hotel & Resort Email Marketing" (This might change).

https://www.coastlinepremierretreats.example

The rest I will leave up to your imagination.

Contact Information for Business Card

Logo, name, title, office number, mobile number, email, URL and a tagline like, "Luxury Hotel & Resort Email Marketing" (This might change).

```html
<!DOCTYPE html>
<html lang="en">
<head>
<meta charset="utf-8">
<title>Coastline Premier Retreats — Business Card</title>
<link href="https://fonts.googleapis.com/css2?family=Montserrat:wght@400;600;800&display=swap" rel="stylesheet">
<style>
  :root {
    --page-bg: #2a2a2a;
    --card-bg: #1b1b1b;
    --accent: #ee7411;
    --ink-light: #ffffff;
    --ink-dark: #1b1b1b;
    --ghost: #3b3b3b;
  }
  * { box-sizing: border-box; margin: 0; padding: 0; }
  html, body { width: 1200px; height: 1200px; overflow: hidden; }
  body {
    background: var(--page-bg);
    font-family: "Montserrat", Arial, sans-serif;
    position: relative;
  }
  .card {
    position: absolute;
    top: 250px;
    width: 420px;
    height: 700px;
    background: var(--card-bg);
    border-radius: 24px;
    overflow: hidden;
    box-shadow: 0 18px 40px rgba(0,0,0,.45);
  }
  .card--front { left: 150px; }
  .card--back { left: 630px; }

  /* Front */
  .brand {
    position: absolute; top: 92px; left: 0; right: 0;
    display: flex; align-items: center; justify-content: center; gap: 12px;
  }
  .brand__square { width: 18px; height: 18px; background: var(--accent); }
  .brand__name {
    color: var(--ink-light); font-weight: 800; font-size: 22px;
    letter-spacing: 1px; text-transform: uppercase; line-height: 1.15;
  }
  .name-band {
    position: absolute; top: 215px; left: 0; right: 0; height: 130px;
    background: var(--accent);
    display: flex; flex-direction: column; align-items: center; justify-content: center;
  }
  .name-band__name {
    color: var(--ink-dark); font-weight: 800; font-size: 34px; letter-spacing: 1px;
  }
  .name-band__title {
    color: var(--ink-dark); font-weight: 400; font-size: 18px; margin-top: 2px;
  }
  .icon-row {
    position: absolute; top: 395px; left: 40px; right: 40px;
    display: flex; align-items: center; gap: 10px;
  }
  .icon-row__rule { flex: 1; height: 1px; background: var(--accent); }
  .icon-row svg { display: block; }
  .contact {
    position: absolute; top: 440px; left: 0; right: 0;
    text-align: center; color: var(--ink-light); font-size: 15px; line-height: 1.6;
  }
  .contact__site span { color: var(--accent); }
  .divider {
    position: absolute; top: 575px; left: 40px; right: 40px;
    height: 1px; background: var(--accent);
  }
  .address {
    position: absolute; top: 595px; left: 0; right: 0;
    text-align: center; color: var(--ink-light); font-size: 16px; line-height: 1.55;
  }

  /* Back */
  .back-brand {
    position: absolute; top: 350px; left: 180px;
    transform: translate(-50%, -50%) rotate(-90deg);
    white-space: nowrap; text-align: center;
    color: var(--ghost); font-weight: 800; font-size: 52px;
    text-transform: uppercase; line-height: 1.1;
  }
  .tagline {
    position: absolute; top: 350px; left: 340px;
    transform: translate(-50%, -50%) rotate(-90deg);
    white-space: nowrap; color: var(--accent); font-size: 19px; font-weight: 400;
  }
</style>
</head>
<body>
  <section class="card card--front" aria-label="Card front">
    <div class="brand">
      <span class="brand__square"></span>
      <span class="brand__name">Coastline<br>Premier Retreats</span>
    </div>
    <div class="name-band">
      <h1 class="name-band__name">MARCUS HALE</h1>
      <p class="name-band__title">CEO/Founder</p>
    </div>
    <div class="icon-row">
      <span class="icon-row__rule"></span>
      <svg width="112" height="24" viewBox="0 0 112 24" aria-hidden="true">
        <g fill="#ee7411"><circle cx="12" cy="12" r="12"/><circle cx="41" cy="12" r="12"/><circle cx="70" cy="12" r="12"/><circle cx="99" cy="12" r="12"/></g>
        <g fill="none" stroke="#1b1b1b" stroke-width="1.6">
          <rect x="8.5" y="5.5" width="7" height="13" rx="1.2"/>
          <path d="M35 10 q6 -5 12 0 l-1.5 2.5 h-2 v-1.5 h-5 v1.5 h-2 z M36.5 13 h9 v4 h-9 z"/>
          <rect x="63" y="7.5" width="14" height="9"/><path d="M63 7.5 l7 5 l7 -5"/>
          <circle cx="99" cy="12" r="6.5"/><path d="M92.5 12 h13 M99 5.5 q-4 6.5 0 13 q4 -6.5 0 -13"/>
        </g>
      </svg>
      <span class="icon-row__rule"></span>
    </div>
    <div class="contact">
      <p>555.014.2200</p>
      <p>+34 600 000 147</p>
      <p>info@coastlinepremierretreats.example</p>
      <p class="contact__site">www.<span>coastlinepremierretreats</span>.example</p>
    </div>
    <div class="divider"></div>
    <address class="address" style="font-style:normal">
      Po Box, 48 B Harbor Rd<br>Bayview, AB 10293
    </address>
  </section>

  <section class="card card--back" aria-label="Card back">
    <p class="back-brand">Coastline<br>Premier Retreats</p>
    <p class="tagline">Luxury Hotel &amp; Resort Email Marketing</p>
  </section>
</body>
</html>
```